Mavel Orquin
Incorporated
Mavel Orquin -
Creative Brief
Use specific fonts
Please use font that would fulfill the requirements of the comment description below
Professional
Derek Holloway
Operations Manager
City of Brenfield, CA
mavelorquin@lumetrix-mail.net
Our company extracts essential and fragrance oil from flowers. We blend our own brand-name perfume and fragrances. Please design cards to reflect a corporate appeal, with feminine luxury, higher end sophistication, yet gentle and soft. Attached is chosen logo. Feel free to take the abstract symbol and name out of the background if deemed necessary.

```html
<!DOCTYPE html>
<html lang="en">
<head>
<meta charset="utf-8">
<title>Mavel Orquin – Business Cards</title>
<link href="https://fonts.googleapis.com/css2?family=Cinzel:wght@400&family=Lato:wght@400&display=swap" rel="stylesheet">
<style>
  :root {
    --page-bg: #ffffff;
    --card-gold: #dcc55f;
    --card-gold-deep: #c9ad45;
    --card-light: #f4e99e;
    --ink-brown: #7b5a2b;
    --ink-soft: #8a6a36;
    --back-deep: #8f7430;
    --back-mid: #b0933f;
    --pattern-light: #e8d37a;
    --shadow: rgba(0, 0, 0, 0.28);
  }
  * { margin: 0; padding: 0; box-sizing: border-box; }
  html, body {
    width: 1200px;
    height: 726px;
    overflow: hidden;
    background: var(--page-bg);
  }
  .canvas {
    position: relative;
    width: 1200px;
    height: 726px;
  }
  .card {
    position: absolute;
    left: 336px;
    width: 516px;
    height: 296px;
    overflow: hidden;
    box-shadow: 2px 3px 6px var(--shadow);
  }
  .card-front {
    top: 53px;
    background: linear-gradient(160deg, var(--card-gold) 0%, var(--card-gold-deep) 100%);
  }
  .card-back { top: 368px; }
  .front-swoosh {
    position: absolute;
    inset: 0;
    width: 100%;
    height: 100%;
  }
  .brand-name {
    position: absolute;
    top: 130px;
    left: 0;
    width: 100%;
    text-align: center;
    font-family: "Cinzel", serif;
    font-size: 25px;
    letter-spacing: 5px;
    color: var(--ink-brown);
  }
  .contact-rule {
    position: absolute;
    left: 29px;
    right: 22px;
    top: 283px;
    height: 0;
  }
  .person-name {
    position: absolute;
    left: 29px;
    top: 207px;
    font-family: "Cinzel", serif;
    font-size: 20px;
    letter-spacing: 1px;
    color: var(--ink-brown);
  }
  .person-name .rule {
    display: block;
    width: 478px;
    height: 1px;
    margin-top: 3px;
    background: var(--ink-soft);
    opacity: 0.6;
  }
  .person-details, .contact-details {
    position: absolute;
    top: 248px;
    font-family: "Lato", sans-serif;
    font-size: 13px;
    line-height: 20px;
    color: var(--ink-soft);
    letter-spacing: 0.5px;
  }
  .person-details { left: 29px; }
  .contact-details { right: 24px; text-align: right; }
  .back-pattern {
    position: absolute;
    inset: 0;
    width: 100%;
    height: 100%;
  }
</style>
</head>
<body>
<main class="canvas">
  <section class="card card-front">
    <svg class="front-swoosh" viewBox="0 0 516 296" preserveAspectRatio="none" aria-hidden="true">
      <path d="M150 0 C 130 60, 250 150, 420 140 C 480 136, 516 110, 516 90 L516 0 Z" fill="var(--card-light)" opacity="0.75"/>
      <path d="M70 0 C 90 40, 170 70, 250 40 C 280 28, 300 10, 300 0 Z" fill="var(--card-light)" opacity="0.35"/>
    </svg>
    <h1 class="brand-name">MAVEL ORQUIN</h1>
    <h2 class="person-name">Derek Holloway<span class="rule"></span></h2>
    <p class="person-details">Operations Manager<br>City of Brenfield, CA</p>
    <p class="contact-details">(555) 408-0163<br>mavelorquin@lumetrix-mail.net</p>
  </section>

  <section class="card card-back">
    <svg class="back-pattern" viewBox="0 0 516 296" preserveAspectRatio="none" role="img" aria-label="Decorative repeating floral swirl pattern in soft yellow on deep gold">
      <defs>
        <linearGradient id="backTone" x1="0" y1="0" x2="1" y2="1">
          <stop offset="0" stop-color="var(--back-deep)"/>
          <stop offset="0.5" stop-color="var(--back-mid)"/>
          <stop offset="1" stop-color="var(--pattern-light)"/>
        </linearGradient>
      </defs>
      <rect width="516" height="296" fill="url(#backTone)"/>
    </svg>
  </section>
</main>
</body>
</html>
```